Wordpress Design Project for Bankruptcy Law Office in San Francisco

our current website: www.dorvanelilaw-example.com

we would like to re-design it for wordpress to make it faster and a bit more modern.

content should be similar to what we have there right now but also we do family law

please include logo for law office:

Law Office of Marta K. Dolvenidze

Thank you.
Updates

please see attached word document with logos that we like as an example.

we do tend to like color red.  darker red.

Please submit your design variations and logo as soon as possible.   We would like to go over them and make our decision

Reason: Please create couple of more variations of logo for your design, so we can make our decision what we like the most. Please see word doc for samples: Text: Law Office Of Marta K. Dolvenidze

Reason: final touches

Target Market(s)

bankruptcy and family law clients

Industry/Entity Type

Family Law

Requirements
Must have
• see examples of law sites
http://promo.lexorbin-example.com/testimonials

- new logo: Law Office of Marta K. Dolvenidze
- client intake form
- blog
- contact us form

Nice to have
• - map
- red color
- on the front page a nice photo of SF or a happy family

```html
<!DOCTYPE html>
<html lang="en">
<head>
<meta charset="utf-8">
<title>Law Office of Marta K. Dolvenidze</title>
<link href="https://fonts.googleapis.com/css2?family=Cinzel&family=Oswald:wght@300&family=PT+Sans:wght@400;700&family=Chewy&family=Arimo&display=swap" rel="stylesheet">
<style>
:root{
  --bg:#ececec;
  --red-top:#dc0a1d;
  --red-bottom:#a3111c;
  --green:#78b60e;
  --form-red:#d65356;
  --card-red:#8e2430;
  --card-red-dark:#7a1d27;
  --heading:#cc5a5e;
  --text:#2a2a2a;
  --footer-top:#7f1f29;
  --footer-bottom:#a72b37;
  --yellow:#f6d21a;
  --white:#ffffff;
}
*{box-sizing:border-box;margin:0;padding:0}
html,body{width:1011px;height:1200px;overflow:hidden}
body{background:var(--bg);font-family:"PT Sans",sans-serif;color:var(--text);position:relative}
.page{position:absolute;left:97px;top:17px;width:817px;height:1160px;background:var(--white);box-shadow:0 0 12px rgba(0,0,0,.25)}
.site-header{position:absolute;left:0;top:0;width:817px;height:91px;background:linear-gradient(var(--red-top),var(--red-bottom))}
.brand{position:absolute;left:22px;top:28px;display:flex;align-items:center;gap:12px;color:var(--white);font-family:"Cinzel",serif}
.brand-mark{width:28px;height:28px;border-radius:50%;background:var(--white)}
.brand-name{font-size:18px;line-height:20px}
.brand-name span{display:block}
.phone{position:absolute;right:10px;top:51px;display:flex;align-items:center;gap:7px;color:var(--white);font-family:"Cinzel",serif;font-size:23px}
.main-nav{position:absolute;left:0;top:91px;width:817px;height:37px;background:var(--green);display:flex;align-items:center}
.main-nav a{position:absolute;color:var(--white);text-decoration:none;font-family:"Oswald",sans-serif;font-weight:300;font-size:15px;text-transform:uppercase;top:9px}
.hero{position:absolute;left:17px;top:149px;width:786px;height:325px;background:linear-gradient(180deg,#2f8fc4 0%,#6fb5d5 30%,#8bbf6a 55%,#5ea21e 80%,#4a8e17 100%)}
.hero-title{position:absolute;left:48px;top:92px;font-family:"Chewy",sans-serif;font-size:46px;line-height:66px;color:var(--white);text-shadow:2px 2px 0 #1f4f36,-1px -1px 0 #1f4f36,1px -1px 0 #1f4f36,-1px 1px 0 #1f4f36,3px 4px 4px rgba(0,0,0,.35)}
.hero-title span{display:block}
.hero-title span+span{padding-left:52px}
.contact-form{position:absolute;left:17px;top:493px;width:202px;height:282px;background:var(--form-red);border:2px dotted #8a8a8a;color:var(--white)}
.contact-form h2{position:absolute;left:12px;top:10px;font-size:14px;font-weight:700}
.contact-form .note{position:absolute;left:19px;top:46px;font-size:11px}
.field{position:absolute;left:12px;width:172px;height:22px;border-radius:3px;background:linear-gradient(#fafafa,#cfcfcf);color:#222;font-size:11px;padding:4px 7px}
.field.message{height:59px;background:linear-gradient(#f3f3f3,#d3d3d3)}
.submit{position:absolute;left:128px;top:262px;width:55px;height:21px;background:#111;color:var(--white);font-size:11px;text-align:center;line-height:21px;border-radius:3px 3px 0 0}
.intro{position:absolute;left:235px;top:490px;width:560px}
.intro h1{font-size:16px;font-weight:700;color:var(--heading);margin-left:-2px}
.intro h2{font-size:15px;font-weight:700;color:var(--heading);margin-top:10px}
.intro p{font-size:11px;line-height:18.5px;text-align:justify;margin-top:6px}
.intro p+p{margin-top:18px}
.intro h2+p{margin-top:0}
.cards{position:absolute;left:0;top:795px}
.card{position:absolute;top:0;width:251px;height:206px;background:linear-gradient(var(--card-red-dark),var(--card-red) 40%,#a02a37);border-radius:6px;color:var(--white);box-shadow:0 6px 6px -3px rgba(0,0,0,.5)}
.card h3{position:absolute;left:20px;top:16px;font-weight:400;font-size:22px}
.card .photo{position:absolute;left:18px;top:47px;width:211px;height:52px;background:linear-gradient(90deg,#5a5a5a,#d9c7b3 45%,#b7cde0)}
.card p{position:absolute;left:16px;top:105px;width:217px;font-family:"Arimo",sans-serif;font-size:10.2px;line-height:13.5px;text-align:justify}
.card .more{position:absolute;right:10px;bottom:11px;font-family:"Arimo",sans-serif;font-size:10px;color:var(--yellow);font-weight:700}
.site-footer{position:absolute;left:0;top:1039px;width:817px;height:121px;background:linear-gradient(var(--footer-top),var(--footer-bottom));color:var(--white);font-family:"Arimo",sans-serif;font-size:10px}
.footer-links{position:absolute;left:19px;top:18px}
.footer-links span{margin-right:9px}
.disclaimer{position:absolute;left:19px;top:50px;width:570px;line-height:15.2px}
.badge{position:absolute;left:711px;top:24px;width:91px;height:67px;background:var(--white);box-shadow:5px 5px 0 rgba(255,255,255,.35)}
.badge i{position:absolute;left:12px;top:9px;width:38px;height:50px;background:#4a82c3}
</style>
</head>
<body>
<div class="page">
  <header class="site-header">
    <div class="brand">
      <span class="brand-mark"></span>
      <div class="brand-name"><span>Law Office of</span><span>Marta K. Dolvenidze</span></div>
    </div>
    <div class="phone">
      <svg width="22" height="22" viewBox="0 0 22 22" aria-hidden="true"><rect width="22" height="22" rx="3" fill="#fff"/><path d="M7 4c1 0 2 3 2 4s-2 1-1 3 2 3 3 3 1-2 2-1 3 1 3 2-1 3-3 3C8 18 4 12 4 8c0-2 2-4 3-4z" fill="#b0131f"/></svg>
      415-555-0182
    </div>
  </header>
  <nav class="main-nav">
    <a href="#" style="left:84px">Home</a>
    <a href="#" style="left:173px">About Us</a>
    <a href="#" style="left:266px">Areas of Practice</a>
    <a href="#" style="left:416px">Resources</a>
    <a href="#" style="left:529px">Blog</a>
    <a href="#" style="left:609px">FAQ</a>
    <a href="#" style="left:679px">Contact Us</a>
  </nav>
  <section class="hero" role="img" aria-label="Child blowing a dandelion in a green meadow">
    <div class="hero-title"><span>Always Protecting</span><span>Client's Interests!</span></div>
  </section>
  <form class="contact-form">
    <h2>CONTACT FORM</h2>
    <div class="note">Fields marked with * are required.</div>
    <div class="field" style="top:71px">Name *</div>
    <div class="field" style="top:102px">Email *</div>
    <div class="field" style="top:132px">Phone</div>
    <div class="field" style="top:163px">Subject *</div>
    <div class="field message" style="top:193px">Message *</div>
    <div class="submit">SUBMIT</div>
  </form>
  <section class="intro">
    <h1>Welcome to Bay Debt Law - Complete Bankruptcy Information</h1>
    <p>The Law Offices of Marta K. Dolvenidze is a consumer law office dedicated to consumer protection and zealously defending the rights of our clients. We offer the big firm quality legal representation with a small firm individualized attention to each client.</p>
    <p>Our office offers services in: all types of consumer bankruptcy filings, i.e. Chapter 7, Chapter 13, Chapter 11, negotiating a settlement of your debts, assisting you in the defense of collection litigation and defending you against foreclosure. Please review our site and see what we may be able to offer you. Feel free to call us at (415) 555-0182 or use our free case evaluation form.</p>
    <h2>Speak to a Lawyer</h2>
    <p>Unlike some other law firms, when you call the Law Office of Marta K. Dolvenidze you will speak to an actual attorney. Not a paralegal or assistant. And even after retaining our office you will still speak to an attorney unlike other firms where you cannot get a hold of your attorney after several attempts.</p>
  </section>
  <section class="cards">
    <article class="card" style="left:16px">
      <h3>Debt Relief</h3>
      <div class="photo" role="img" aria-label="Couple meeting with an attorney"></div>
      <p>This page is available, however, but because occasionally circumstances occur in which toil and pain can procure him some great. To take a trivial example, which of us ever undertakes laborious physical exercise, except to obtain some advantage from it.</p>
      <span class="more">read more...</span>
    </article>
    <article class="card" style="left:283px">
      <h3>Foreclosure Prevention</h3>
      <div class="photo" role="img" aria-label="Happy family in a car"></div>
      <p>This page is available, however, but because occasionally circumstances occur in which toil and pain can procure him some great. To take a trivial example, which of us ever undertakes laborious physical exercise, except to obtain some advantage from it.</p>
      <span class="more">read more...</span>
    </article>
    <article class="card" style="left:549px">
      <h3>Chapter 13</h3>
      <div class="photo" role="img" aria-label="Relieved couple at a laptop"></div>
      <p>This page is available, however, but because occasionally circumstances occur in which toil and pain can procure him some great. To take a trivial example, which of us ever undertakes laborious physical exercise, except to obtain some advantage from it.</p>
      <span class="more">read more...</span>
    </article>
  </section>
  <footer class="site-footer">
    <div class="footer-links"><span>Go to top</span><span>Copyright © 2010 MKDLaw. All Rights Reserved. | Web Development by Webfield</span></div>
    <p class="disclaimer">Disclaimer: The Law Offices of Marta K. Dolvenidze is a Debt Relief law firm as defined by 11 U.S.C. 528. We help people file for Bankruptcy Relief under the Bankruptcy Code. The information contained on this website is not to be construed as legal advice. It is not intended to solicit or form an attorney-client relationship. We do not guarantee any result and prior results do not guarantee a similar outcome. This is an attorney advertisement and this website is for informational purposes only.</p>
    <div class="badge" role="img" aria-label="Professional association membership badge"><i></i></div>
  </footer>
</div>
</body>
</html>
```